Marwick Law Letterhead

We need a new letterhead design for a Law Firm. The address for the law firm is 1475 Calloway Street, Suite 210, Houston, Texas 77041. Phone Number: 832-361-9027; Fax Number: 832-614-7359. The logo is uploaded to the project.

```html
<!DOCTYPE html>
<html lang="en">
<head>
<meta charset="utf-8">
<title>Marwick Law Letterhead</title>
<link href="https://fonts.googleapis.com/css2?family=Montserrat:wght@400;500;600&display=swap" rel="stylesheet">
<style>
  :root {
    --backdrop: #e8e8e8;
    --paper: #ffffff;
    --ink: #1c1c1c;
    --navy: #1d2f6b;
    --red: #d5121e;
    --red-dark: #7c0a10;
    --signature-tone: #ececec;
  }
  * { margin: 0; padding: 0; box-sizing: border-box; }
  html, body {
    width: 1200px; height: 960px; overflow: hidden;
    background: var(--backdrop);
    font-family: "Montserrat", sans-serif;
    color: var(--ink);
  }
  .letterhead {
    position: absolute; left: 282px; top: 30px;
    width: 636px; height: 900px;
    background: var(--paper);
    box-shadow: 0 2px 10px rgba(0,0,0,0.12);
    overflow: hidden;
  }
  .brand {
    position: absolute; left: 44px; top: 48px;
    display: flex; align-items: center; gap: 10px;
  }
  .brand-dot { width: 22px; height: 22px; border-radius: 50%; background: var(--navy); }
  .brand-name { font-size: 24px; font-weight: 600; color: var(--navy); letter-spacing: 0.5px; }
  .letter-date {
    position: absolute; right: 60px; top: 100px;
    font-size: 9.5px; font-weight: 500;
  }
  .recipient {
    position: absolute; left: 130px; top: 138px;
    font-size: 9.5px; line-height: 1.4; font-style: normal;
  }
  .letter-body {
    position: absolute; left: 130px; top: 198px; width: 460px;
    font-size: 9.5px; line-height: 1.4;
  }
  .letter-body p { margin-bottom: 11px; }
  .sign-off {
    position: absolute; left: 130px; top: 682px;
    font-size: 11px; font-weight: 500;
  }
  .signature {
    position: absolute; left: 136px; top: 702px;
    width: 110px; height: 32px;
    background: var(--signature-tone); border-radius: 4px;
  }
  .footer-band {
    position: absolute; left: 260px; top: 750px;
    width: 230px; height: 24px;
  }
  .footer-rule {
    position: absolute; left: 0; right: 0; top: 774px;
    height: 1px; background: var(--red);
  }
  .contact-phones {
    position: absolute; left: 300px; top: 790px;
    display: flex; gap: 18px; font-size: 10.5px; font-weight: 500;
  }
  .contact-phones span { display: flex; align-items: center; gap: 6px; }
  .contact-address {
    position: absolute; left: 260px; top: 816px;
    font-size: 10.5px; font-weight: 500;
  }
</style>
</head>
<body>
  <main class="letterhead">
    <header class="brand">
      <span class="brand-dot"></span>
      <span class="brand-name">Marwick Law</span>
    </header>

    <p class="letter-date">DATE:05-Jan-2022</p>

    <address class="recipient">
      M/s<br>First Name and Last Name<br>Company Name<br>Address
    </address>

    <section class="letter-body">
      <p>Lorem ipsum dolor sit amet,consectetur adipiscing sed do eiusmod tempor incididunt laboreet dolore magna aliqua.Ut enim ad minim.veniam, quis nostrud exercitation ullamco laboris nisi ut aliquip exea commodo consequat.Lorem ipsum dolor sit amet,consectetur adipiscing sed do eiusmod tempor incididunt.labore et dolore magna aliqua. Ut enim</p>
      <p>Lorem ipsum dolor sit amet, consectetur adipiscing sed do eiusmod tempor incididunt labore et dolore magna aliqua. Ut enim ad minim veniam, quis nostrud exercitation ullamco laboris nisi ut aliquip exea commodo consequat.Duis aute irure dolor in reprehenderit in voluptate velit esse cillum irure dolor in reprehenderit in voluptate velit esse irure</p>
      <p>Lorem ipsum dolor sit amet, consectetur adipiscing sed do eiusmod tempor incididunt labore et dolore magna aliqua. consequat. Duis aute irure dolor in.reprehenderit in voluptate velit esse cillum dolore eu fugiat nulla pariatur. Excepteur sint occaecat cupidatat non proident, sunt in culpa qui officia deserunt mollit,</p>
      <p>Lorem ipsum dolor sit amet, consectetur adipiscing sed do eiusmod tempor incididunt labore et dolore magna aliqua. Ut enim Lorem ipsum dolor sit amet, consectetur adipiscing sed do eiusmod tempor incididunt labore et dolore magna aliqua. Ut enim Lorem ipsum aliqua.ipsum</p>
      <p>Lorem ipsum dolor sit amet, consectetur adipiscing sed do eiusmod tempor incididunt labore et dolore magna aliqua. Ut enim ad minim veniam, quis nostrud exercitation ullamco laboris nisi ut aliquip exea commodo consequat.Duis aute irure dolor in reprehenderit in voluptate velit esse cillum irure dolor in reprehenderit in voluptate velit esse irure</p>
      <p>Lorem ipsum dolor sit amet, consectetur adipiscing sed do eiusmod tempor incididunt labore et dolore magna aliqua. Ut enim ad minim veniam, quis nostrud exercitation ullamco laboris nisi ut aliquip exea commodo consequat.Duis aute irure dolor in reprehenderit in voluptate velit esse cillum irure dolor in reprehenderit in voluptate velit esse irure</p>
    </section>

    <p class="sign-off">Regards</p>
    <div class="signature" role="img" aria-label="Handwritten signature"></div>

    <svg class="footer-band" viewBox="0 0 230 24" aria-hidden="true">
      <defs>
        <linearGradient id="bandFill" x1="0" x2="1" y1="0" y2="0">
          <stop offset="0" stop-color="#d5121e"/>
          <stop offset="1" stop-color="#7c0a10"/>
        </linearGradient>
      </defs>
      <polygon points="0,24 14,0 230,0 216,24" fill="url(#bandFill)"/>
    </svg>
    <div class="footer-rule"></div>

    <div class="contact-phones">
      <span>
        <svg width="12" height="12" viewBox="0 0 24 24" aria-hidden="true"><path fill="#d5121e" d="M6.6 10.8a15.1 15.1 0 0 0 6.6 6.6l2.2-2.2a1 1 0 0 1 1-.25 11.4 11.4 0 0 0 3.6.57 1 1 0 0 1 1 1V20a1 1 0 0 1-1 1A17 17 0 0 1 3 4a1 1 0 0 1 1-1h3.5a1 1 0 0 1 1 1c0 1.25.2 2.45.57 3.57a1 1 0 0 1-.25 1z"/></svg>
        832-361-9027
      </span>
      <span>
        <svg width="12" height="12" viewBox="0 0 24 24" aria-hidden="true"><path fill="#d5121e" d="M6 3h9v5H6zM4 9h16a2 2 0 0 1 2 2v6h-4v4H6v-4H2v-6a2 2 0 0 1 2-2zm4 8v2h8v-2z"/></svg>
        832-614-7359
      </span>
    </div>
    <p class="contact-address">1475 Calloway Street, Suite 210, Houston, Texas 77041</p>
  </main>
</body>
</html>
```